Coral Bay Pools New website

I currently operate a swimming pool service and repair business and looking for a re design for my website as it has been over 5 years since it was designed. current site is coralbaypoolslv.com

```html
<!DOCTYPE html>
<html lang="en">
<head>
<meta charset="utf-8">
<title>Coral Bay Pools – Pool Cleaning in Las Vegas</title>
<link href="https://fonts.googleapis.com/css2?family=Montserrat:wght@300;400;500;600;700;800&family=Figtree:wght@400;500;600;700&display=swap" rel="stylesheet">
<style>
:root{
  --navy:#0d3f86;
  --deep:#0b4a9c;
  --blue:#1563b5;
  --sky:#2aa0e3;
  --card:#1e93e6;
  --orange:#f7861e;
  --gold:#f5b622;
  --light:#dcecf9;
  --ink:#1c1c1c;
  --white:#ffffff;
  --black:#000000;
}
*{margin:0;padding:0;box-sizing:border-box}
html,body{width:1200px;height:4057px;overflow:hidden}
body{position:relative;background:var(--white);font-family:"Figtree",sans-serif;color:var(--ink)}
.abs{position:absolute}
.head{font-family:"Montserrat",sans-serif;font-weight:800;text-transform:uppercase}
.btn{position:absolute;display:flex;align-items:center;justify-content:center;font-family:"Montserrat",sans-serif;font-weight:700;text-transform:uppercase;border-radius:5px;color:var(--white);background:var(--orange)}
.eyebrow{position:absolute;display:flex;gap:4px}
.eyebrow .chip{width:25px;height:25px;border-radius:50%;background:var(--navy);border:2px solid var(--gold);color:var(--white);font:700 11px "Montserrat",sans-serif;display:flex;align-items:center;justify-content:center}
.eyebrow .space{width:18px}
.eyebrow.center{left:0;right:0;justify-content:center}
.accent{color:var(--sky)}

/* hero */
.hero-photo{left:0;top:0;width:1200px;height:700px;background:linear-gradient(180deg,#1a3560 0%,#2a4a6a 12%,#1e3a22 22%,#2c4a24 40%,#3f6a2a 52%,#5b7f35 56%,#7a6f5e 60%,#2fb8c8 64%,#3fc6d4 78%,#2aa6b8 86%,#8a7565 90%,#6e5c50 100%)}
.brand{display:flex;align-items:center;gap:8px;font-family:"Montserrat",sans-serif;font-weight:800;color:var(--white);font-size:18px}
.brand .dot{width:22px;height:22px;border-radius:50%;background:var(--orange)}
.nav{left:470px;top:38px;display:flex;align-items:center;font:600 14px "Montserrat",sans-serif;color:var(--white);text-transform:uppercase}
.nav .item{padding:10px 12px}
.nav .home{border:1.5px solid var(--white);border-radius:6px;padding:9px 14px;margin-right:8px}
.nav .gap{margin-right:16px}
.hero-title{left:0;width:1200px;top:155px;text-align:center;color:var(--white);font-size:41px;line-height:50px;letter-spacing:.5px}
.hero-title .hl{color:var(--orange)}
.dots{left:565px;top:594px;display:flex;gap:7px}
.dots span{width:9px;height:9px;border-radius:50%;background:var(--white)}
.dots span:first-child{background:var(--orange)}

/* about */
.before-after{left:153px;top:748px;width:409px;height:488px;border-radius:14px;overflow:hidden}
.before-after .brand-top{position:absolute;left:0;top:0;width:409px;height:180px;background:var(--white);display:flex;align-items:center;justify-content:center;gap:12px;font:800 30px "Montserrat",sans-serif;color:var(--navy)}
.brand-top .dot{width:30px;height:30px;border-radius:50%;background:var(--orange)}
.ba-before{position:absolute;left:0;top:180px;width:205px;height:308px;background:linear-gradient(160deg,#2e3b1e,#4d5a2a 60%,#3a3a28)}
.ba-after{position:absolute;left:205px;top:180px;width:204px;height:308px;background:linear-gradient(160deg,#4fd0d6,#2ab4c4 60%,#6fc7c9)}
.ba-label{position:absolute;bottom:16px;font:700 17px "Montserrat",sans-serif;color:var(--white)}
.about-title{left:617px;top:790px;font-size:28px;line-height:38px;color:var(--navy)}
.about-title .accent{color:var(--sky)}
.about-text{left:617px;top:966px;width:430px;font-size:12.5px;line-height:21px;text-align:justify}
.about-text b{color:var(--navy)}

/* services */
.services{left:0;top:1291px;width:1200px;height:665px;background:radial-gradient(ellipse at 30% 30%,#1d6fc0 0%,transparent 55%),radial-gradient(ellipse at 80% 70%,#1a69ba 0%,transparent 55%),var(--blue)}
.sec-title{left:0;width:1200px;text-align:center;font-size:27px}
.rule{height:2px;width:48px;background:var(--white)}
.svc{top:1482px;width:285px;height:439px;background:var(--card);border-radius:12px;overflow:hidden}
.svc .photo{height:263px}
.svc h3{margin:22px 0 0 26px;font:400 20px "Montserrat",sans-serif;color:var(--white);text-transform:uppercase}
.svc p{margin:8px 26px 0;font-size:11.5px;line-height:17.5px;color:#eaf4ff}
.svc .btn{left:26px;top:384px;width:112px;height:32px;font-size:10px}

/* why */
.why-strip{left:1157px;top:1956px;width:43px;height:740px;background:var(--blue)}
.why-panel{left:0;top:1956px;width:1157px;height:740px;background:var(--white);border-top-right-radius:44px}
.why-div{left:369px;top:2013px;width:2px;height:60px;background:#c9d6e6}
.why-title{left:409px;top:2026px;font-size:27px;color:var(--navy)}
.why-photo{left:157px;top:2110px;width:437px;height:512px;border-radius:10px;background:linear-gradient(145deg,#bfe4f6,#8ccff0 40%,#5bb8e8 70%,#a6dcf4)}
.why-text{left:632px;top:2114px;width:410px;font-size:12.5px;line-height:21px;text-align:justify}
.feat{left:632px;width:420px;display:flex;gap:20px}
.feat .ic{width:56px;height:56px;border-radius:50%;background:var(--orange);flex:none;display:flex;align-items:center;justify-content:center}
.feat h4{font:800 13px "Montserrat",sans-serif;color:var(--navy);text-transform:uppercase;margin-top:4px}
.feat p{font-size:12px;line-height:18px;margin-top:6px;width:300px}

/* testimonials */
.testi-bg{left:0;top:2696px;width:1200px;height:780px;background:var(--light)}
.testi-title{left:0;width:1200px;top:2796px;text-align:center;font-size:28px;color:var(--navy)}
.arrow{left:87px;width:46px;height:46px;border-radius:50%;display:flex;align-items:center;justify-content:center}
.tcard{top:2887px;width:291px;height:290px;background:var(--white);border-radius:10px;padding:16px 22px 0 22px}
.tcard .who{display:flex;align-items:center;gap:16px}
.tcard .avatar{width:82px;height:82px;border-radius:50%;background:linear-gradient(160deg,#cfd6df,#8a96a6)}
.tcard .name{font:600 16px "Montserrat",sans-serif}
.tcard .stars{color:var(--gold);font-size:20px;letter-spacing:1px;margin-top:4px}
.tcard .quote{position:absolute;right:22px;top:22px;font:800 44px "Montserrat",sans-serif;color:var(--blue);line-height:1}
.tcard p{margin-top:26px;font-size:12.5px;line-height:21px}

/* contact */
.black-wave{left:0;top:3420px;width:1200px;height:637px}
.contact-card{left:150px;top:3273px;width:900px;height:401px;border-radius:18px;background:radial-gradient(ellipse at 25% 30%,#1a66b8 0%,transparent 55%),radial-gradient(ellipse at 75% 70%,#175fae 0%,transparent 55%),var(--deep)}
.contact-title{left:0;width:900px;top:98px;text-align:center;font-size:28px;line-height:37px;color:var(--white)}
.contact-text{left:0;width:900px;top:222px;text-align:center;font-size:15px;line-height:25px;color:#d6e6f7}

/* footer */
.footer-brand{left:158px;top:3790px;font-size:20px}
.social{top:3894px;width:36px;height:36px;border-radius:50%;background:var(--orange)}
.fcol{color:var(--white)}
.fcol h5{font:700 16px "Montserrat",sans-serif;text-transform:uppercase;margin-bottom:14px}
.fcol li{list-style:none;font-size:14px;height:30px;display:flex;align-items:center;gap:12px}
.fcol li::before{content:"";width:9px;height:9px;border-top:2px solid var(--white);border-right:2px solid var(--white);transform:rotate(45deg)}
.fcontact{display:flex;align-items:center;gap:14px;font-size:14px;color:var(--white)}
.fcontact .ci{width:26px;height:26px;border-radius:50%;background:var(--white);display:flex;align-items:center;justify-content:center}
.f-rule{left:150px;top:3985px;width:900px;height:1px;background:#cfcfcf}
.copy{left:0;width:1200px;top:4008px;text-align:center;color:var(--white);font-size:12px}
</style>
</head>
<body>

<!-- HERO -->
<div class="abs hero-photo" role="img" aria-label="Rectangular backyard swimming pool surrounded by lawn and tall evergreen trees under a blue sky"></div>
<div class="abs brand" style="left:150px;top:52px"><span class="dot"></span>Coral Bay Pools</div>
<nav class="abs nav">
  <span class="item home">Home</span>
  <span class="item gap">About Us</span>
  <span class="item gap">Services</span>
  <span class="btn" style="position:relative;width:140px;height:38px;font-size:12px;margin-right:20px">Free Estimate</span>
  <span class="btn" style="position:relative;width:120px;height:38px;font-size:12px;background:var(--navy)">Contact Us</span>
</nav>
<h1 class="abs head hero-title">Nevada’s <span class="hl">Most Trusted</span><br>Local Pool Cleaning</h1>
<a class="btn" style="left:425px;top:280px;width:162px;height:44px;font-size:14px">Free Estimate</a>
<a class="btn" style="left:606px;top:280px;width:114px;height:44px;font-size:14px;background:transparent;border:2px solid var(--orange);color:var(--orange)">Call Us</a>
<div class="abs dots"><span></span><span></span><span></span><span></span></div>
<svg class="abs" style="left:0;top:620px" width="1200" height="80" viewBox="0 0 1200 80">
  <path d="M0 40 C200 75 420 82 640 70 S980 30 1200 8 L1200 80 L0 80 Z" fill="#ffffff"/>
  <path d="M0 40 C200 75 420 82 640 70 S980 30 1200 8" fill="none" stroke="#0d3f86" stroke-width="3"/>
</svg>

<!-- ABOUT -->
<div class="abs before-after">
  <div class="brand-top"><span class="dot"></span>Coral Bay Pools</div>
  <div class="ba-before" role="img" aria-label="Green murky pool water before cleaning"></div>
  <div class="ba-after" role="img" aria-label="Clear turquoise pool water after cleaning"></div>
  <span class="ba-label" style="left:16px">BEFORE</span>
  <span class="ba-label" style="right:20px">AFTER</span>
</div>
<div class="eyebrow" style="left:613px;top:746px">
  <span class="chip">A</span><span class="chip">B</span><span class="chip">O</span><span class="chip">U</span><span class="chip">T</span><span class="space"></span><span class="chip">U</span><span class="chip">S</span>
</div>
<h2 class="abs head about-title"><span class="accent">Trusted Pool Repair</span><br>&amp; Service Experts<br>in Las Vegas</h2>
<p class="abs about-text">When you need professional pool cleaning services in Nevada, you can count on the professionals at Coral Bay Pools to provide you with superior and prompt solutions. Whether you need assistance with a <b>residential</b> or <b>commercial pool</b>, we’ll vacuum, brush, and thoroughly clean your pool so it’s swim-ready. We’ll also clean your pool filters and inform you of any issues that arise. Our staff is certified by the Clark Valley Health District to ensure proper chemical levels and equipment are safe. To learn more about our pool cleaning services or to get your free estimate, contact our pool experts today.</p>
<a class="btn" style="left:619px;top:1192px;width:151px;height:44px;font-size:14px">Learn More</a>

<!-- SERVICES -->
<section class="abs services"></section>
<div class="eyebrow center" style="top:1342px">
  <span class="chip">S</span><span class="chip">E</span><span class="chip">R</span><span class="chip">V</span><span class="chip">I</span><span class="chip">C</span><span class="chip">E</span><span class="chip">S</span>
</div>
<h2 class="abs head sec-title" style="top:1386px;color:var(--white)">Our <span class="accent">Pool Service</span> in Las Vegas</h2>
<div class="abs rule" style="left:576px;top:1442px"></div>

<article class="abs svc" style="left:151px">
  <div class="photo" role="img" aria-label="Technician skimming a backyard pool with a long net pole" style="background:linear-gradient(180deg,#6f9a4a,#4c7a32 55%,#3aa6d6 72%,#2a8cc8)"></div>
  <h3>Pool Service</h3>
  <p>When you invested in your pool, you knew it was a long-term investment in both money and time.</p>
  <a class="btn">Learn More</a>
</article>
<article class="abs svc" style="left:458px">
  <div class="photo" role="img" aria-label="Modern commercial building beside a large blue pool" style="background:linear-gradient(180deg,#dfe8ef,#9a8a78 40%,#4a4440 55%,#1f5fae 70%,#164b94)"></div>
  <h3>Commercial Pool</h3>
  <p>As a commercial property owner or manager, doing your job well requires you to be mindful of all the details.</p>
  <a class="btn">Learn More</a>
</article>
<article class="abs svc" style="left:765px">
  <div class="photo" role="img" aria-label="White family home with a long backyard pool" style="background:linear-gradient(180deg,#cfe2f2,#f0f0ee 30%,#b9b6ae 55%,#6bbbe0 72%,#3f9fd4)"></div>
  <h3>Residentiaal Pool</h3>
  <p>As a commercial property owner or manager, doing your job well requires you to be mindful of all the details.</p>
  <a class="btn">Learn More</a>
</article>

<!-- WHY US -->
<div class="abs why-strip"></div>
<div class="abs why-panel"></div>
<div class="eyebrow" style="left:154px;top:2031px">
  <span class="chip">W</span><span class="chip">H</span><span class="chip">Y</span><span class="space"></span><span class="chip">U</span><span class="chip">S</span>
</div>
<div class="abs why-div"></div>
<h2 class="abs head why-title">Why <span class="accent">Las Vegas</span> Chooses Coral Bay</h2>
<div class="abs why-photo" role="img" aria-label="Blue automatic pool vacuum head and hose on the floor of a clear pool"></div>
<p class="abs why-text">Our full-service pool company proudly serves the entire Las Vegas valley, and we’re certified by the Clark Valley Health District to maintain the highest level of pool safety. If you need pool repairs, maintenance, scheduled cleanings, or any other pool services, contact us online or by phone today.</p>

<div class="abs feat" style="top:2259px">
  <div class="ic"><svg width="28" height="28" viewBox="0 0 28 28" fill="none" stroke="#fff" stroke-width="2"><circle cx="10" cy="10" r="5"/><path d="M14 14 L24 24"/></svg></div>
  <div><h4>Expert Technicians</h4><p>Certified and experienced in all major pool systems and brands.</p></div>
</div>
<div class="abs feat" style="top:2357px">
  <div class="ic"><svg width="28" height="28" viewBox="0 0 28 28" fill="none" stroke="#fff" stroke-width="2"><circle cx="14" cy="14" r="9"/><path d="M14 8 V14 L18 17"/></svg></div>
  <div><h4>Fast, Reliable Service</h4><p>We know pool problems can’t wait, so we offer prompt scheduling and on-time arrivals.</p></div>
</div>
<div class="abs feat" style="top:2456px">
  <div class="ic"><svg width="28" height="28" viewBox="0 0 28 28" fill="none" stroke="#fff" stroke-width="2"><path d="M4 14 L14 4 H24 V14 L14 24 Z"/><circle cx="19" cy="9" r="2"/></svg></div>
  <div><h4>Honest Pricing</h4><p>No hidden fees, just clear estimates and upfront communication.</p></div>
</div>
<div class="abs feat" style="top:2553px">
  <div class="ic"><svg width="28" height="28" viewBox="0 0 28 28" fill="none" stroke="#fff" stroke-width="2"><rect x="6" y="4" width="16" height="20" rx="2"/><path d="M10 10 H18 M10 15 H18 M10 20 H15"/></svg></div>
  <div><h4>Local &amp; Licensed</h4><p>Proudly serving Las Vegas, Henderson, Summerlin, and North Las Vegas.</p></div>
</div>

<!-- TESTIMONIALS -->
<div class="abs testi-bg"></div>
<div class="eyebrow center" style="top:2751px">
  <span class="chip">T</span><span class="chip">E</span><span class="chip">S</span><span class="chip">T</span><span class="chip">I</span><span class="chip">M</span><span class="chip">O</span><span class="chip">N</span><span class="chip">I</span><span class="chip">A</span><span class="chip">L</span><span class="chip">S</span>
</div>
<h2 class="abs head testi-title"><span class="accent">What Our</span> Clients Say</h2>
<div class="abs arrow" style="top:2968px;background:var(--white)"><svg width="22" height="22" viewBox="0 0 22 22" fill="none" stroke="#1563b5" stroke-width="2.5"><path d="M18 11 H4 M10 5 L4 11 L10 17"/></svg></div>
<div class="abs arrow" style="top:3034px;background:var(--blue)"><svg width="22" height="22" viewBox="0 0 22 22" fill="none" stroke="#fff" stroke-width="2.5"><path d="M4 11 H18 M12 5 L18 11 L12 17"/></svg></div>

<article class="abs tcard" style="left:151px">
  <div class="who"><div class="avatar" role="img" aria-label="Customer portrait"></div><div><div class="name">Dana R</div><div class="stars">★★★★★</div></div></div>
  <span class="quote">“</span>
  <p>Lorem Ipsum is simply dummy text of the printing and typesetting industry. Lorem Ipsum has been the industry’s standard dummy text ever since the 1500s, when an unknown printer took a galley of type and scrambled it to make a type specimen book.</p>
</article>
<article class="abs tcard" style="left:457px">
  <div class="who"><div class="avatar" role="img" aria-label="Customer portrait"></div><div><div class="name">Marisol</div><div class="stars">★★★★★</div></div></div>
  <span class="quote">“</span>
  <p>Lorem Ipsum is simply dummy text of the printing and typesetting industry. Lorem Ipsum has been the industry’s standard dummy text ever since the 1500s, when an unknown printer took a galley of type and scrambled it to make a type specimen book.</p>
</article>
<article class="abs tcard" style="left:761px">
  <div class="who"><div class="avatar" role="img" aria-label="Customer portrait"></div><div><div class="name">Grant</div><div class="stars">★★★★★</div></div></div>
  <span class="quote">“</span>
  <p>Lorem Ipsum is simply dummy text of the printing and typesetting industry. Lorem Ipsum has been the industry’s standard dummy text ever since the 1500s, when an unknown printer took a galley of type and scrambled it to make a type specimen book.</p>
</article>

<!-- CONTACT BAND -->
<svg class="abs black-wave" width="1200" height="637" viewBox="0 0 1200 637">
  <path d="M0 70 C60 30 140 20 220 30 L980 30 C1060 20 1140 30 1200 60 L1200 637 L0 637 Z" fill="#000"/>
</svg>
<section class="abs contact-card">
  <div class="eyebrow center" style="top:57px">
    <span class="chip">C</span><span class="chip">O</span><span class="chip">N</span><span class="chip">T</span><span class="chip">A</span><span class="chip">C</span><span class="chip">T</span><span class="space"></span><span class="chip">U</span><span class="chip">S</span>
  </div>
  <h2 class="abs head contact-title">Keep Your Pool Crystal Clear —<br><span class="accent">Without the Hassle</span></h2>
  <div class="abs rule" style="left:426px;top:188px"></div>
  <p class="abs contact-text">Professional pool cleaning, maintenance, and repair services you can trust in the<br>Las Vegas Valley.</p>
  <a class="btn" style="left:293px;top:282px;width:308px;height:43px;font-size:14px">Get Your Free Estimate Today!</a>
</section>

<!-- FOOTER -->
<div class="abs brand footer-brand"><span class="dot"></span>Coral Bay Pools</div>
<span class="abs social" style="left:184px" aria-label="Social profile"></span>
<span class="abs social" style="left:236px" aria-label="Social profile"></span>
<span class="abs social" style="left:288px" aria-label="Social profile"></span>

<div class="abs fcol" style="left:402px;top:3731px">
  <h5>Quick Links</h5>
  <ul><li>Home</li><li>About Us</li><li>Our Services</li><li>Free Estimate</li><li>Contact</li><li>Blog</li></ul>
</div>
<div class="abs fcol" style="left:575px;top:3731px">
  <h5>Help Links</h5>
  <ul><li>Privacy Policy</li><li>Careers</li><li>Terms and Conditions</li></ul>
</div>
<div class="abs fcol" style="left:803px;top:3731px">
  <h5>Contact Us</h5>
</div>
<div class="abs fcontact" style="left:803px;top:3775px">
  <span class="ci"><svg width="14" height="14" viewBox="0 0 24 24" fill="#000"><path d="M6.6 10.8a15 15 0 0 0 6.6 6.6l2.2-2.2a1 1 0 0 1 1-.25 11.4 11.4 0 0 0 3.6.57 1 1 0 0 1 1 1V20a1 1 0 0 1-1 1A17 17 0 0 1 3 4a1 1 0 0 1 1-1h3.5a1 1 0 0 1 1 1c0 1.250.2 2.450.57 3.570a1 1 0 0 1-.25 1z"/></svg></span>(702) 555-0148
</div>
<div class="abs fcontact" style="left:803px;top:3821px">
  <span class="ci"><svg width="14" height="14" viewBox="0 0 24 24" fill="none" stroke="#000" stroke-width="2.2"><rect x="3" y="5" width="18" height="14" rx="2"/><path d="M3 7 L12 13 L21 7"/></svg></span>poolsolutions@coralbaypoolslv.com
</div>
<div class="abs f-rule"></div>
<p class="abs copy">© 2026 Coral Bay&nbsp; I All Rights Reserved</p>

</body>
</html>
```